BildeVOLD buisnesscard

Hey :) I need a modern buisnesscard for my company BildeVOLD
It most have:
Dagligleder og Fotograf: Henrik Audun Strandvik

Mob: +4791264085
Epost: post@bildevold.example
Adresse: Kvernbakken9, 6040 Fjordvik

Facbook and instagram logo with text BildeVOLD

BildeVOLD logo

It Company

```html
<!DOCTYPE html>
<html lang="no">
<head>
<meta charset="utf-8">
<title>BildeVOLD – visittkort</title>
<link rel="stylesheet" href="https://fonts.googleapis.com/css2?family=Noto+Sans:wght@400;700&display=swap">
<style>
  :root {
    --backdrop: #7a4f2d;
    --card: #252525;
    --ink: #a9a9a9;
    --ink-strong: #b8b8b8;
    --icon-fg: #252525;
  }
  * { box-sizing: border-box; margin: 0; padding: 0; }
  html, body { width: 1200px; height: 1200px; overflow: hidden; }
  body {
    background: var(--backdrop);
    font-family: "Noto Sans", Verdana, sans-serif;
    color: var(--ink);
    position: relative;
  }
  .card {
    position: absolute;
    width: 720px;
    height: 434px;
    background: var(--card);
  }
  .card--front { left: 240px; top: 106px; }
  .card--back { left: 238px; top: 624px; }

  .holder { position: absolute; left: 50px; top: 44px; }
  .holder__name { font-size: 27px; color: var(--ink-strong); font-weight: 400; letter-spacing: 0.3px; line-height: 1.2; }
  .holder__role { font-size: 16px; margin-top: 4px; letter-spacing: 0.3px; }

  .contact { position: absolute; left: 50px; top: 290px; list-style: none; }
  .contact li { display: flex; align-items: center; height: 37.5px; font-size: 19px; letter-spacing: 0.4px; }
  .contact svg { width: 29px; height: 29px; margin-right: 30px; flex: none; }

  .address { position: absolute; left: 466px; top: 344px; display: flex; align-items: flex-start; }
  .address svg { width: 28px; height: 28px; margin-right: 18px; margin-top: 2px; }
  .address p { font-size: 19px; line-height: 23px; letter-spacing: 0.4px; }

  .brand {
    position: absolute; left: 0; right: 0; top: 236px;
    text-align: center; font-size: 46px; font-weight: 700; color: var(--ink);
    letter-spacing: 0.5px; line-height: 1.2;
  }
  .social { position: absolute; left: 0; right: 0; top: 332px; display: flex; justify-content: center; gap: 26px; }
  .social__item { display: flex; align-items: center; font-size: 19px; letter-spacing: 0.4px; }
  .social__item .dot { width: 32px; height: 32px; border: 2px solid var(--ink); border-radius: 50%; margin-right: 10px; }
</style>
</head>
<body>
  <section class="card card--front">
    <header class="holder">
      <h1 class="holder__name">Henrik Audun Strandvik</h1>
      <p class="holder__role">Dagligleder og Fotograf</p>
    </header>

    <ul class="contact">
      <li>
        <svg viewBox="0 0 30 30" aria-hidden="true"><circle cx="15" cy="15" r="15" fill="var(--ink)"/><path d="M10 7.5l3 0 1.5 4-2 1.5c1 2.2 2.5 3.7 4.5 4.5l1.5-2 4 1.5v3c0 1-1 2-2 2C13.5 22 8 16.5 8 9.5c0-1 1-2 2-2z" fill="var(--icon-fg)"/></svg>
        <span>479 126 4085</span>
      </li>
      <li>
        <svg viewBox="0 0 30 30" aria-hidden="true"><circle cx="15" cy="15" r="15" fill="var(--ink)"/><circle cx="15" cy="15" r="9" fill="none" stroke="var(--icon-fg)" stroke-width="2"/><ellipse cx="15" cy="15" rx="4" ry="9" fill="none" stroke="var(--icon-fg)" stroke-width="1.8"/><path d="M6 15h18M7.5 10.5h15M7.5 19.5h15" stroke="var(--icon-fg)" stroke-width="1.6"/></svg>
        <span>www.bildevold.example</span>
      </li>
      <li>
        <svg viewBox="0 0 30 30" aria-hidden="true"><circle cx="15" cy="15" r="15" fill="var(--ink)"/><rect x="8" y="10" width="14" height="10" fill="var(--icon-fg)"/><path d="M8 10l7 6 7-6" fill="none" stroke="var(--ink)" stroke-width="1.4"/></svg>
        <span>post@bildevold.example</span>
      </li>
    </ul>

    <div class="address">
      <svg viewBox="0 0 30 30" aria-hidden="true"><circle cx="15" cy="15" r="15" fill="var(--ink)"/><path d="M15 7a5.5 5.5 0 0 0-5.5 5.5c0 4 5.5 10 5.5 10s5.5-6 5.5-10A5.5 5.5 0 0 0 15 7z" fill="var(--icon-fg)"/><circle cx="15" cy="12.5" r="2" fill="var(--ink)"/></svg>
      <p>Kvernbakken9<br>6040 Fjordvik</p>
    </div>
  </section>

  <section class="card card--back">
    <p class="brand">BildeVOLD</p>
    <div class="social">
      <div class="social__item"><span class="dot"></span>BildeVOLD</div>
      <div class="social__item"><span class="dot"></span>BildeVOLD</div>
    </div>
  </section>
</body>
</html>
```